KVOR Individual and Corporate Development Business Card Design

KVOR needs a business card design that is aligned with it's values and targetted markets. Coherent Lattice of Adaptive Reasoning Method's self diagnosis model and tools, which can be used for personal improvement and team/business performance enhancement, is based on the learnings of over 20 years of medical practitioning. KVOR supercharges personal effectiveness and awareness to also increase team and business performance.

The targetted markets are high performance individuals and teams who aspire seek to enhance their capabilities and achieve their absolute best potential.

Look and feel for the business card design we are looking for is high technology, premium, fresh, new and medical.

Target Market(s)

Industry/Entity Type

Business Consultant

Contact Information for Business Card

Logo, Full Name, Title, Phone number, Email, company name, Address,

Font styles to use
Sans Serif

Requirements
Must have
• Tag line: Maximising Performance for Highly Effective People
• Please use same colours as the logo.

```html
<!DOCTYPE html>
<html lang="en">
<head>
<meta charset="utf-8">
<title>KVOR Business Card</title>
<link href="https://fonts.googleapis.com/css2?family=Exo+2:wght@400;500;600;700&display=swap" rel="stylesheet">
<style>
  :root {
    --teal: #00a7c2;
    --ink: #000000;
    --slate: #5f6368;
    --rule: #a9acb1;
    --paper: #ffffff;
    --stage: #2b2b2d;
  }
  * { box-sizing: border-box; margin: 0; padding: 0; }
  html, body { width: 1200px; height: 880px; overflow: hidden; }
  body {
    background: var(--stage);
    font-family: "Exo 2", Arial, sans-serif;
    position: relative;
  }
  .card {
    position: absolute;
    left: 290px;
    width: 620px;
    height: 354px;
    border-radius: 18px;
    overflow: hidden;
  }
  .card--back { top: 48px; background: var(--ink); }
  .card--front { top: 478px; background: var(--paper); }

  .brand {
    position: absolute;
    left: 0; right: 0;
    text-align: center;
  }
  .brand__name {
    display: inline-flex;
    align-items: center;
    gap: 14px;
    font-size: 74px;
    font-weight: 700;
    letter-spacing: 6px;
    color: var(--teal);
    line-height: 1;
  }
  .brand__dot {
    width: 18px; height: 18px;
    border-radius: 50%;
    background: var(--teal);
  }
  .brand__rule {
    width: 300px;
    height: 2px;
    margin: 10px auto 8px;
    background: var(--slate);
  }
  .brand__full {
    font-size: 15px;
    font-weight: 600;
    letter-spacing: 1.5px;
    text-transform: uppercase;
    color: var(--teal);
    line-height: 1.2;
  }
  .card--back .brand { top: 96px; }
  .card--front .brand { top: 40px; }

  .back__band {
    position: absolute;
    left: 0; right: 0;
    top: 268px;
    height: 58px;
    background: var(--teal);
    border-bottom: 3px solid var(--paper);
    display: flex;
    align-items: center;
    padding-left: 34px;
  }
  .tagline {
    color: var(--paper);
    font-size: 19px;
    font-weight: 500;
    letter-spacing: 0.6px;
  }

  .front__rule {
    position: absolute;
    left: 0; right: 0;
    top: 206px;
    height: 4px;
    background: var(--rule);
  }
  .front__band {
    position: absolute;
    left: 0; right: 0;
    top: 216px;
    height: 82px;
    background: var(--teal);
    border-bottom: 4px solid var(--paper);
    display: flex;
    align-items: center;
    color: var(--paper);
  }
  .person {
    width: 190px;
    text-align: right;
    padding-right: 18px;
  }
  .person__name { font-size: 19px; font-weight: 500; letter-spacing: 0.5px; }
  .person__title { font-size: 16px; }
  .divider {
    width: 1.5px;
    height: 40px;
    background: var(--paper);
  }
  .contact {
    padding: 0 18px;
    font-size: 15px;
    line-height: 1.45;
  }
  .contact__row { display: flex; align-items: center; gap: 7px; }
  .contact__row svg { width: 16px; height: 16px; flex: none; }
  .address {
    padding-left: 18px;
    font-size: 15px;
    line-height: 1.45;
  }
  .front__foot {
    position: absolute;
    left: 0; right: 0;
    top: 302px;
    bottom: 0;
    background: var(--slate);
    display: flex;
    align-items: center;
    justify-content: center;
    color: var(--paper);
    font-size: 16px;
    font-weight: 600;
    letter-spacing: 2px;
    text-transform: uppercase;
  }
</style>
</head>
<body>

<section class="card card--back" aria-label="Card back">
  <div class="brand">
    <div class="brand__name"><span>KVOR</span><span class="brand__dot"></span></div>
    <div class="brand__rule"></div>
    <div class="brand__full">Coherent Lattice of<br>Adaptive Reasoning Method</div>
  </div>
  <div class="back__band">
    <p class="tagline">Maximising Performance for Highly Effective People</p>
  </div>
</section>

<section class="card card--front" aria-label="Card front">
  <div class="brand">
    <div class="brand__name"><span>KVOR</span><span class="brand__dot"></span></div>
    <div class="brand__rule"></div>
    <div class="brand__full">Coherent Lattice of<br>Adaptive Reasoning Method</div>
  </div>
  <div class="front__rule"></div>
  <div class="front__band">
    <div class="person">
      <div class="person__name">LENA HARTWELL</div>
      <div class="person__title">Founder</div>
    </div>
    <div class="divider"></div>
    <div class="contact">
      <div class="contact__row">
        <svg viewBox="0 0 16 16" aria-hidden="true"><circle cx="8" cy="8" r="7" fill="none" stroke="#fff" stroke-width="1.3"/><rect x="5.5" y="3.5" width="5" height="9" rx="1" fill="none" stroke="#fff" stroke-width="1.2"/></svg>
        <span>(555) 210-4836</span>
      </div>
      <div class="contact__row">
        <svg viewBox="0 0 16 16" aria-hidden="true"><circle cx="8" cy="8" r="7" fill="none" stroke="#fff" stroke-width="1.3"/><rect x="4" y="5.2" width="8" height="5.6" fill="none" stroke="#fff" stroke-width="1.1"/><path d="M4 5.4 L8 8.6 L12 5.4" fill="none" stroke="#fff" stroke-width="1.1"/></svg>
        <span>hello@kvormail.com</span>
      </div>
    </div>
    <div class="divider"></div>
    <div class="address">
      <div>PO BOX 418 Harbour Lane</div>
      <div>7th street Ashford</div>
    </div>
  </div>
  <div class="front__foot">Coherent Lattice of Adaptive Reasoning Method</div>
</section>

</body>
</html>
```